Ad for Cyber Security Company- Print Ad

We are looking for an awesome designer to create a one page advertisement for the Kelvora Security data analytics platform that will be featured in an upcoming security magazine. This is also going to be featured in an upcoming trade show. Kelvora Security produced the KELVORA platform to help companies unify their security environment and help them address Insider Threat, Fraud and Anomaly ID and resolution. KELVORA uses an an advanced ingestion engine, machine learning, and workflow automation to ensure the right people are getting the right info at the right time. We serve enterprise level customers, augmenting and enhancing, not replacing their existing security stack. We would like few or single image, clean, and open ad built around the tagline 'Make Security a Team Sport.' We would like the logo to be featured, and include our website address on the page (www.kelvorasecurity.net). See below for style guide.

Target Market(s)

Industry insiders, Chief Information Security Officers (CISO) and Technical directors.

Other font styles liked:
• See style guide, but we are open to suggestion.

Requirements
Must have
• A single image (minimum), Feature the provided logo, Include the tagline 'Make Security a Team Sport' and have the website somewhere on the ad. The image should focus on the conveying the message of "Make Security a Team Sport" and not be a generic security (padlock, network, etc.) image.
• See included style guide.

```html
<!DOCTYPE html>
<html lang="en">
<head>
<meta charset="utf-8">
<title>Kelvora Security – Make Security a Team Sport</title>
<link rel="stylesheet" href="https://fonts.googleapis.com/css2?family=Orbitron:wght@900&family=Open+Sans:wght@300;600;800&display=swap">
<style>
  :root {
    --orange: #f26522;
    --orange-bright: #ff6a1f;
    --charcoal: #2b2b2d;
    --charcoal-deep: #1f1f21;
    --ink: #111111;
    --logo-grey: #3a3a3c;
    --white: #ffffff;
    --photo-deep: #0a1626;
    --photo-navy: #13304f;
    --photo-blue: #1f5e9c;
    --photo-cyan: #3fa3e0;
    --photo-slate: #5c6d80;
  }
  * { margin: 0; padding: 0; box-sizing: border-box; }
  html, body {
    width: 960px; height: 1200px; overflow: hidden;
    background: var(--charcoal);
  }
  .ad {
    position: relative; width: 960px; height: 1200px; overflow: hidden;
    font-family: "Open Sans", Arial, sans-serif;
  }
  .header {
    position: absolute; left: 0; top: 0; width: 960px; height: 217px;
    background: linear-gradient(115deg, #e6e6e7 0%, #f5f5f5 45%, #ffffff 100%);
    display: flex; align-items: center; justify-content: center; gap: 20px;
  }
  .brand-mark {
    width: 82px; height: 82px; background: var(--orange);
  }
  .brand-name {
    display: flex; flex-direction: column;
    font-family: "Orbitron", "Arial Black", sans-serif; font-weight: 900;
    font-size: 42px; letter-spacing: 2px; color: var(--logo-grey);
    text-transform: uppercase; line-height: 1.02;
  }
  .team-photo {
    position: absolute; left: 0; top: 217px; width: 960px; height: 540px;
    background:
      radial-gradient(ellipse 38% 32% at 70% 24%, rgba(63,163,224,0.75) 0%, transparent 100%),
      radial-gradient(ellipse 26% 30% at 12% 22%, rgba(63,163,224,0.6) 0%, transparent 100%),
      radial-gradient(ellipse 22% 36% at 47% 42%, rgba(92,109,128,0.55) 0%, transparent 100%),
      radial-gradient(ellipse 30% 26% at 90% 30%, rgba(31,94,156,0.7) 0%, transparent 100%),
      linear-gradient(180deg, var(--photo-blue) 0%, var(--photo-navy) 45%, var(--photo-deep) 100%);
  }
  .lower {
    position: absolute; left: 0; top: 755px; width: 960px; height: 357px;
    background: linear-gradient(160deg, #363638 0%, var(--charcoal) 50%, var(--charcoal-deep) 100%);
    border-top: 3px solid var(--orange);
  }
  .tagline-banner {
    position: absolute; left: 0; top: 0; width: 960px; height: 1200px; pointer-events: none;
  }
  .tagline {
    position: absolute; left: 94px; top: 672px; width: 770px; height: 195px;
    display: flex; flex-direction: column; align-items: center; justify-content: center;
    font-family: "Orbitron", "Arial Black", sans-serif; font-weight: 900;
    font-size: 48px; line-height: 1.08; letter-spacing: 2px; word-spacing: 14px;
    text-transform: uppercase; color: var(--ink);
  }
  .tagline .accent { color: var(--orange); }
  .features {
    position: absolute; left: 0; top: 920px; width: 960px;
  }
  .feature {
    position: absolute; top: 0; width: 300px; margin-left: -150px;
    display: flex; flex-direction: column; align-items: center;
  }
  .feature-icon {
    width: 88px; height: 88px; border-radius: 50%; background: var(--orange);
    border: 2px solid #ffffff; display: flex; align-items: center; justify-content: center;
  }
  .feature-label {
    margin-top: 24px; font-weight: 600; font-size: 24px; color: var(--white);
    white-space: nowrap;
  }
  .feature-rule {
    margin-top: 8px; width: 32px; height: 4px; background: var(--orange);
  }
  .footer {
    position: absolute; left: 0; top: 1112px; width: 960px; height: 88px;
    background: var(--orange-bright);
    display: flex; align-items: center; justify-content: center;
    color: var(--white); font-size: 27px; letter-spacing: 10px;
  }
  .footer .light { font-weight: 300; }
  .footer .bold { font-weight: 800; }
</style>
</head>
<body>
<div class="ad">
  <header class="header">
    <div class="brand-mark"></div>
    <div class="brand-name"><span>Kelvora</span><span>Security</span></div>
  </header>

  <div class="team-photo" role="img" aria-label="Photo of a security team briefing in a control room, a presenter addressing analysts at desks in front of world map screens and monitors"></div>

  <section class="lower"></section>

  <svg class="tagline-banner" width="960" height="1200" viewBox="0 0 960 1200" aria-hidden="true">
    <defs>
      <linearGradient id="bannerFill" x1="0" y1="0" x2="1" y2="1">
        <stop offset="0" stop-color="#ffffff"/>
        <stop offset="0.55" stop-color="#ececec"/>
        <stop offset="1" stop-color="#c9cacc"/>
      </linearGradient>
    </defs>
    <polygon points="146,672 864,672 812,867 94,867" fill="url(#bannerFill)"/>
  </svg>

  <h1 class="tagline">
    <span>Make <span class="accent">Security</span> A</span>
    <span class="accent">Team Sport</span>
  </h1>

  <div class="features">
    <div class="feature" style="left:229px">
      <div class="feature-icon">
        <svg width="50" height="50" viewBox="0 0 50 50" fill="none" stroke="#fff" stroke-width="2">
          <rect x="4" y="6" width="38" height="34"/>
          <line x1="4" y1="13" x2="42" y2="13"/>
          <line x1="9" y1="19" x2="22" y2="19"/>
          <line x1="9" y1="25" x2="18" y2="25"/>
          <line x1="9" y1="31" x2="20" y2="31"/>
          <circle cx="32" cy="26" r="7"/>
          <line x1="37" y1="31" x2="45" y2="40"/>
        </svg>
      </div>
      <div class="feature-label">Anomaly Detection</div>
      <div class="feature-rule"></div>
    </div>
    <div class="feature" style="left:476px">
      <div class="feature-icon">
        <svg width="50" height="50" viewBox="0 0 50 50" fill="none" stroke="#fff" stroke-width="2">
          <rect x="4" y="6" width="42" height="28"/>
          <line x1="20" y1="34" x2="18" y2="42"/>
          <line x1="12" y1="42" x2="26" y2="42"/>
          <circle cx="22" cy="19" r="8"/>
          <line x1="28" y1="25" x2="38" y2="36"/>
        </svg>
      </div>
      <div class="feature-label">Insider Threat</div>
      <div class="feature-rule"></div>
    </div>
    <div class="feature" style="left:733px">
      <div class="feature-icon">
        <svg width="50" height="50" viewBox="0 0 50 50" fill="none" stroke="#fff" stroke-width="2">
          <rect x="10" y="4" width="26" height="34"/>
          <line x1="15" y1="12" x2="31" y2="12"/>
          <line x1="15" y1="18" x2="26" y2="18"/>
          <rect x="4" y="26" width="36" height="16"/>
          <circle cx="32" cy="28" r="7"/>
          <line x1="37" y1="33" x2="45" y2="42"/>
        </svg>
      </div>
      <div class="feature-label">User Activity Reviews</div>
      <div class="feature-rule"></div>
    </div>
  </div>

  <footer class="footer">
    <span class="light">www.</span><span class="bold">KelvoraSecurity</span><span class="light">.net</span>
  </footer>
</div>
</body>
</html>
```